Podiatry (services) Business Card

I need a business design for a New Podiatry Service.
the Podiatry services will include all aspects of podiatry including;
general podiatry for all ages
corns and callus treatment
Ingrown toenails & nail surgery
Forefoot, arch and heel pain
Gait analysis
Sports Podiatry and Orthotics
Paediatric Assessments
Diabetes Foot Assessment

I would like the back of the card to have space for next appointment day and time.

I would like a nice design that is simple yet catchy. I don't like cluttered business cards. I like things to be simple yet stand out because of the finer details.

I like the colours blue and white but I'm open to other designs that have different colours.

Business

Bluewren Podiatry (Business name)

Marisol Tenbury - Podiatrist
M.Pod.P., B.Hlth. Sci, MFLsoc

Address: 58 Coleby St, Marrowdale North Vic, 3164
Phone: (03) 9416 2738
Fax: (03) 9523 4178

```html
<!DOCTYPE html>
<html lang="en">
<head>
<meta charset="utf-8">
<title>Bluewren Podiatry – Business Card</title>
<link rel="stylesheet" href="https://fonts.googleapis.com/css2?family=Source+Sans+3:wght@400;600&display=swap">
<style>
  :root {
    --stage: #3a3431;
    --card-black: #111213;
    --brand-blue: #1b7fcc;
    --brand-blue-bright: #2b95e0;
    --white: #ffffff;
    --text-light: #e6e6e6;
    --divider: #2a5f8c;
    --font: "Source Sans 3", sans-serif;
  }
  * { box-sizing: border-box; margin: 0; padding: 0; }
  html, body {
    width: 1200px; height: 844px; overflow: hidden;
    background: var(--stage);
    font-family: var(--font);
  }
  .stage {
    position: relative; width: 1200px; height: 844px;
    display: flex; align-items: center; justify-content: center; gap: 60px;
  }
  .card {
    position: relative; width: 510px; height: 292px; overflow: hidden;
    box-shadow: 0 10px 28px rgba(0,0,0,.45);
  }

  /* Front */
  .card-front { background: var(--card-black); display: flex; }
  .front-brand {
    width: 235px; display: flex; align-items: center; justify-content: center; gap: 10px;
  }
  .brand-dot { width: 14px; height: 14px; border-radius: 50%; background: var(--brand-blue); flex: none; }
  .brand-name { color: var(--brand-blue); font-size: 24px; font-weight: 400; letter-spacing: .5px; line-height: 1.1; }
  .front-divider {
    width: 1px; margin: 34px 0;
    background: linear-gradient(to bottom, transparent, var(--divider) 20%, var(--divider) 80%, transparent);
  }
  .front-details { padding: 44px 0 0 18px; color: var(--text-light); font-size: 13px; line-height: 1.35; }
  .practitioner { font-size: 17px; }
  .practitioner-name { color: var(--brand-blue-bright); font-weight: 600; }
  .credentials { margin-bottom: 16px; }
  .address { margin-bottom: 18px; }
  .contact-line { display: flex; align-items: center; gap: 7px; font-size: 14px; margin-bottom: 3px; }
  .contact-line svg { width: 11px; height: 11px; fill: var(--brand-blue-bright); flex: none; }

  /* Back */
  .card-back { background: var(--white); }
  .back-band {
    position: absolute; left: 0; top: 0; width: 100%; height: 178px;
    background: var(--brand-blue); display: flex;
  }
  .back-brand { width: 220px; display: flex; align-items: center; justify-content: center; gap: 9px; }
  .back-brand .brand-dot { background: var(--white); }
  .back-brand .brand-name { color: var(--white); font-size: 21px; }
  .back-divider {
    width: 1px; margin: 22px 0;
    background: linear-gradient(to bottom, transparent, rgba(255,255,255,.45) 20%, rgba(255,255,255,.45) 80%, transparent);
  }
  .service-list { list-style: none; padding: 20px 0 0 18px; color: var(--white); font-size: 12.5px; line-height: 1.38; }
  .service-list li { display: flex; align-items: center; gap: 7px; }
  .service-list li::before { content: ""; width: 5px; height: 5px; border-radius: 50%; background: var(--white); flex: none; }
  .appointment {
    position: absolute; left: 0; top: 178px; width: 100%; height: 114px;
    color: var(--brand-blue); padding: 20px 26px 0;
  }
  .appointment-title { text-align: center; font-size: 15px; font-weight: 600; margin-bottom: 34px; }
  .appointment-fields { display: flex; align-items: baseline; font-size: 14px; font-weight: 600; gap: 4px; }
  .field-line { flex: 1; border-bottom: 1.5px dotted var(--brand-blue); height: 1px; }
  .field-line.short { flex: .55; }
</style>
</head>
<body>
<main class="stage">
  <section class="card card-front" aria-label="Card front">
    <div class="front-brand">
      <span class="brand-dot"></span>
      <span class="brand-name">Bluewren Podiatry</span>
    </div>
    <div class="front-divider"></div>
    <div class="front-details">
      <p class="practitioner"><span class="practitioner-name">Marisol Tenbury</span> - Podiatrist</p>
      <p class="credentials">M.Pod.P., B.Hlth. Sci, MFLsoc</p>
      <p class="address">58 Coleby St, Marrowdale<br>North Vic, 3164</p>
      <p class="contact-line">
        <svg viewBox="0 0 24 24" aria-hidden="true"><path d="M6.6 10.8a15 15 0 0 0 6.6 6.6l2.2-2.2a1 1 0 0 1 1-.25 11.4 11.4 0 0 0 3.6.57 1 1 0 0 1 1 1V20a1 1 0 0 1-1 1A17 17 0 0 1 3 4a1 1 0 0 1 1-1h3.5a1 1 0 0 1 1 1c0 1.25.2 2.45.57 3.57a1 1 0 0 1-.25 1z"/></svg>
        (03) 9416 2738
      </p>
      <p class="contact-line">
        <svg viewBox="0 0 24 24" aria-hidden="true"><path d="M7 2h8l3 3v5H7z M4 11h16a2 2 0 0 1 2 2v7a2 2 0 0 1-2 2H4a2 2 0 0 1-2-2v-7a2 2 0 0 1 2-2z"/></svg>
        (03) 9523 4178
      </p>
    </div>
  </section>

  <section class="card card-back" aria-label="Card back">
    <div class="back-band">
      <div class="back-brand">
        <span class="brand-dot"></span>
        <span class="brand-name">Bluewren Podiatry</span>
      </div>
      <div class="back-divider"></div>
      <ul class="service-list">
        <li>General podiatry for all ages</li>
        <li>Corns and callus treatment</li>
        <li>Ingrown toenails &amp; nail surgery</li>
        <li>Forefoot, arch and heel pain</li>
        <li>Gait analysis</li>
        <li>Sports Podiatry and Orthotics</li>
        <li>Paediatric Assessments</li>
        <li>Diabetes Foot Assessment</li>
      </ul>
    </div>
    <div class="appointment">
      <p class="appointment-title">Appointment</p>
      <div class="appointment-fields">
        <span>Name:</span><span class="field-line"></span>
        <span>Date:</span><span class="field-line short"></span>
        <span>Time:</span><span class="field-line short"></span>
      </div>
    </div>
  </section>
</main>
</body>
</html>
```